Powerpoint design template for LUMOTEX for new digital platform

We would like to use a PowerPoint template, we would like to create a new page, we would like to create a new digital platform LUMOTEX for schools and parents for the creation of playful communication and educational tools for children to enhance their positive development, amaze them learn in a playful way. This platform is going to be the most creative, stimulating and innovative classroom, easy to use and fast to implement. Scrapbooking, collages ... Magazine, newsletters Diplomla / awards Slideshows Facebook Calendars Organizers Greetings Games ... This powerpoint template will be used essential to We are looking for a professional design, positioning our brand in the children market with an adult hearing. so you will need to find a good deal. Primary target: nurseries & schools from 0 to 18 years old and universities (in 2nd phase) Secondary target: small & medium businesses Third target: general public, and TPE If it is a color scheme, then it is suggested that it be marketed in Europe (UK, Italy, Spain) and in a 2nd Stage USA and other countries. multiple options for front page, insidious pages (multiple styles with limited text and extended text) and final contact page We need something to read, we can not do it too much, but we can not do it. , and inside pages aligned to our logo

Target Market(s)

Target 1; Education with teacher Target 2; parents and grandparents

Industry/Entity Type

Education

Font styles to use
Other font styles liked:
• not decided. but not too fancy

Requirements
Must have
• Multi page options for front page, page insides (multiple styles with limited text and extended text) and final page contact
Nice to have
• do not have a lot of ideas. We need something to read, we can not get away from it
Should not have
• not too fancy and busy: keep clarity & simplicity while reassuring on quality

```html
<!DOCTYPE html>
<html lang="en">
<head>
<meta charset="utf-8">
<title>Content Title Here</title>
<link href="https://fonts.googleapis.com/css2?family=Catamaran:wght@600;800&family=Mulish:wght@400&display=swap" rel="stylesheet">
<style>
  :root {
    --title-blue: #2393be;
    --body-grey: #4f4f4f;
    --paper: #fdfcf4;
    --paper-shade: #f3f6ea;
    --sky-tint: #eef3e6;
    --meadow-light: #c9e08f;
    --meadow: #9bc54b;
    --meadow-deep: #7fb236;
    --badge-yellow: #f7b41c;
    --badge-pink: #e8317b;
    --badge-ring: #ffffff;
    --brand-ink: #2b2b2b;
    --brand-lime: #c8dc2a;
  }
  html, body {
    margin: 0;
    padding: 0;
    overflow: hidden;
  }
  .slide {
    position: relative;
    width: 1200px;
    height: 900px;
    overflow: hidden;
    background: linear-gradient(180deg, var(--paper) 0%, var(--paper-shade) 100%);
    font-family: "Mulish", Arial, sans-serif;
  }
  .scene-illustration {
    position: absolute;
    left: 0;
    top: 430px;
    width: 1200px;
    height: 470px;
    background:
      radial-gradient(ellipse 900px 220px at 50% 100%, var(--meadow-deep) 0%, var(--meadow) 55%, rgba(155,197,75,0) 100%),
      radial-gradient(ellipse 420px 260px at 50% 62%, rgba(155,197,75,0.35) 0%, rgba(155,197,75,0) 100%),
      radial-gradient(ellipse 180px 200px at 935px 150px, rgba(247,196,60,0.55) 0%, rgba(247,196,60,0) 100%),
      linear-gradient(180deg, rgba(238,243,230,0) 0%, var(--sky-tint) 35%, var(--meadow-light) 78%, var(--meadow) 100%);
  }
  .slide-title {
    position: absolute;
    left: 49px;
    top: 22px;
    margin: 0;
    font-family: "Catamaran", Arial, sans-serif;
    font-weight: 600;
    font-size: 51px;
    letter-spacing: 1.2px;
    color: var(--title-blue);
    line-height: 1.2;
  }
  .brand {
    position: absolute;
    right: 36px;
    top: 46px;
    display: flex;
    align-items: center;
    gap: 10px;
  }
  .brand-mark {
    width: 26px;
    height: 26px;
    background: var(--brand-lime);
  }
  .brand-name {
    font-family: "Catamaran", Arial, sans-serif;
    font-weight: 800;
    font-size: 32px;
    color: var(--brand-ink);
    line-height: 1;
  }
  .points {
    position: absolute;
    left: 0;
    top: 0;
    margin: 0;
    padding: 0;
    list-style: none;
  }
  .point {
    position: absolute;
    left: 68px;
    width: 1080px;
    display: flex;
  }
  .point-one { top: 128px; }
  .point-two { top: 294px; }
  .point-badge {
    flex: none;
    width: 76px;
    height: 76px;
  }
  .point-text {
    margin: 16px 0 0 24px;
    width: 940px;
    font-size: 27.5px;
    line-height: 42px;
    color: var(--body-grey);
  }
  .badge-number {
    font-family: "Catamaran", Arial, sans-serif;
    font-weight: 800;
    font-size: 30px;
    fill: #ffffff;
  }
</style>
</head>
<body>
<main class="slide">
  <div class="scene-illustration" role="img" aria-label="Playful cartoon scene of smiling food characters standing on a green hill with trees, clouds and a yellow balloon"></div>

  <h1 class="slide-title">CONTENT TITLE HERE</h1>

  <div class="brand">
    <span class="brand-mark"></span>
    <span class="brand-name">LUMOTEX</span>
  </div>

  <ol class="points">
    <li class="point point-one">
      <svg class="point-badge" viewBox="0 0 76 76" aria-hidden="true">
        <circle cx="38" cy="38" r="35" fill="var(--badge-ring)" stroke="#e6e6e0" stroke-width="1.5"/>
        <circle cx="38" cy="38" r="26" fill="var(--badge-yellow)"/>
        <text class="badge-number" x="38" y="49" text-anchor="middle">1</text>
      </svg>
      <p class="point-text">Lemon drops oat cake oat cake sugar plum sweet gingerbread chocolate cake gingerbread. Lemon drops oat cake oat cake sugar plum sweet</p>
    </li>
    <li class="point point-two">
      <svg class="point-badge" viewBox="0 0 76 76" aria-hidden="true">
        <circle cx="38" cy="38" r="35" fill="var(--badge-ring)" stroke="#e6e6e0" stroke-width="1.5"/>
        <circle cx="38" cy="38" r="26" fill="var(--badge-pink)"/>
        <text class="badge-number" x="38" y="49" text-anchor="middle">2</text>
      </svg>
      <p class="point-text">Lemon drops oat cake oat cake sugar plum sweet gingerbread chocolate cake gingerbread. Lemon drops oat cake oat cake sugar plum sweet</p>
    </li>
  </ol>
</main>
</body>
</html>
```